Design and Renovation Company Luxury Business Card

I want to create a luxury business card for a Design and Renovation Firm . We will use our current logo. The company name is 528BUILDA. We do not want anything standard. We need a very unique concept.
Please see uploaded inspiration. I really like the textured paper option. I would like the card to be thick with debossing, and/or embossing options. The logo has orange in it but I would like to see the card with and without the orange. I think the orange may make the company feel less high-end. The goal is to elevate the logo not match its vibe per se of the logo. We want something very unique, not standard at all!
I would like a space for :
Logo,
Name,
Position,
Email,
Office number,
Website Address,
Business Address,
Thank you!
Have fun!
Target Market(s)
Home owners Age 35 +
Industry/Entity Type
Design and Renovation
Contact Information for Business Card
Logo, Name, Position, Email, Office number, Website Address, Business Address,.
Colors
Designer to choose colors to be used in the design.
Requirements
Must have
- A luxury designer feel. Must be black or dark grey but open to other luxury ideas.
Nice to have
- Gold, silver, black embossing or debossing. Textured paper design.
Should not have
- A cheap look and feel.

```html
<!DOCTYPE html>
<html lang="en">
<head>
<meta charset="utf-8">
<title>528BUILDA Business Card</title>
<link rel="stylesheet" href="https://fonts.googleapis.com/css2?family=Arimo:wght@400;700&display=swap">
<style>
  :root {
    --backdrop: #c9c9c9;
    --charcoal: #2d2d2d;
    --charcoal-deep: #262626;
    --pattern-dark: #1e1e1e;
    --orange: #e5891e;
    --white: #ffffff;
    --tile-white: #f2f2f2;
    --edge: #e6e6e6;
  }
  * { box-sizing: border-box; margin: 0; padding: 0; }
  html, body { width: 1200px; height: 800px; overflow: hidden; }
  body {
    background: linear-gradient(180deg, #d6d6d6 0%, var(--backdrop) 100%);
    font-family: "Arimo", Arial, sans-serif;
    display: flex;
    align-items: center;
    justify-content: center;
    gap: 40px;
  }
  .card {
    width: 540px;
    height: 310px;
    border-radius: 18px;
    overflow: hidden;
    position: relative;
    box-shadow: 0 0 0 2px var(--edge), 0 10px 24px rgba(0,0,0,0.25);
  }

  /* Front */
  .card-front { display: flex; background: var(--charcoal); }
  .brand-panel {
    width: 245px;
    background: var(--charcoal);
    display: flex;
    align-items: center;
    justify-content: center;
    gap: 12px;
  }
  .brand-square {
    width: 28px; height: 28px;
    background: var(--orange);
  }
  .brand-name {
    color: var(--white);
    font-weight: 400;
    font-size: 30px;
    letter-spacing: 2px;
  }
  .divider {
    width: 8px;
    background: var(--charcoal);
    display: flex;
    justify-content: center;
  }
  .divider::before {
    content: "";
    width: 3px;
    background: var(--tile-white);
  }
  .info-panel {
    flex: 1;
    background: var(--orange);
    color: var(--white);
    padding: 46px 26px 0 34px;
  }
  .person-name { font-weight: 700; font-size: 24px; line-height: 1.1; }
  .person-role { font-size: 15px; margin-top: 2px; }
  .address { font-size: 14px; line-height: 1.35; margin-top: 22px; }
  .contacts { list-style: none; margin-top: 14px; font-size: 14px; line-height: 1.45; }
  .contacts li { display: flex; align-items: center; gap: 8px; }
  .contacts svg { width: 11px; height: 11px; flex: none; fill: var(--white); }

  /* Back */
  .card-back { background: var(--charcoal-deep); }
  .pattern-field {
    position: absolute; inset: 0;
    background: radial-gradient(ellipse at 40% 50%, #2a2a2a 0%, var(--pattern-dark) 100%);
  }
  .back-mark {
    position: absolute;
    right: 34px; top: 138px;
    display: flex; align-items: center; gap: 8px;
  }
  .back-mark .brand-square { width: 14px; height: 14px; }
  .back-mark .brand-name { font-size: 15px; letter-spacing: 1px; }
</style>
</head>
<body>
  <section class="card card-front">
    <div class="brand-panel">
      <span class="brand-square"></span>
      <span class="brand-name">528BUILDA</span>
    </div>
    <div class="divider"></div>
    <div class="info-panel">
      <p class="person-name">Marcus Hale</p>
      <p class="person-role">President</p>
      <p class="address">2417 Alderbrook Lane<br>Glen Ridge, NY 11020</p>
      <ul class="contacts">
        <li><svg viewBox="0 0 12 12"><path d="M2.5 0.5l2 2-1.2 1.5c0.8 1.8 2 3 3.7 3.7l1.5-1.2 2 2-1.3 2C5.3 10.3 1.7 6.7 0.5 1.8z"/></svg>(555) 0142-7789</li>
        <li><svg viewBox="0 0 12 12"><path d="M0 2h12v8H0z M0.8 2.6L6 6.6l5.2-4" stroke="#e5891e" stroke-width="1"/></svg>name@528BUILDA.com</li>
        <li><svg viewBox="0 0 12 12"><circle cx="6" cy="6" r="5.5"/></svg>www.528BUILDA.com</li>
      </ul>
    </div>
  </section>

  <section class="card card-back">
    <div class="pattern-field" role="img" aria-label="Debossed repeating pattern of tonal dark squares across the card back"></div>
    <div class="back-mark">
      <span class="brand-square"></span>
      <span class="brand-name">528BUILDA</span>
    </div>
  </section>
</body>
</html>
```